Property management company looking for modern card design

We at Blue Heron Partners provides property management services for its residential and commercial properties, with expertise in all categories of multifamily, industrial and office projects throughout California.

We need a business card design that is professional and modern designed business card. In our field, clients get hundreds of business cards, we would like our card to stand out.

Please avoid small print.

Target Market(s)

Professionals and high end clients

Industry/Entity Type

Financial Planning

Contact Information for Business Card

Company Name: Blue Heron Partners, Name, email, license #, phone number, website blueheronpartners.com

Font styles to use
Sans Serif

Requirements
Must have
• The card design needs to be adaptable because there is a possibly we will be expanding into different sectors other than real estate. The card design should be focused on financial planning and asset management.
Nice to have
• Modern and simple business card. Eye catching. Non-standard size/shaped cards would be great.
• blueheronpartners.com
Should not have
• Too many bright color or any pictures or shapes of real estate stuff.

```html
<!DOCTYPE html>
<html lang="en">
<head>
<meta charset="utf-8">
<title>Blue Heron Partners – Business Card</title>
<link href="https://fonts.googleapis.com/css2?family=Arimo:wght@400&display=swap" rel="stylesheet">
<style>
  :root {
    --backdrop: #849996;
    --gold: #8e7c3f;
    --navy: #172836;
    --wine: #6e0a0e;
    --white: #ffffff;
  }
  html, body {
    margin: 0;
    padding: 0;
    width: 1200px;
    height: 1200px;
    overflow: hidden;
    background: var(--backdrop);
    font-family: "Arimo", Arial, sans-serif;
  }
  .canvas {
    position: relative;
    width: 1200px;
    height: 1200px;
  }
  .card {
    position: absolute;
    left: 244px;
    width: 666px;
  }
  .card-front {
    top: 146px;
    height: 380px;
    background: var(--gold);
  }
  .brand-name {
    position: absolute;
    left: 0;
    right: 0;
    top: 50%;
    transform: translateY(-50%);
    margin: 0;
    text-align: center;
    font-size: 58px;
    font-weight: 400;
    color: var(--wine);
    letter-spacing: 1px;
  }
  .card-back {
    top: 636px;
    height: 382px;
    background: var(--navy);
  }
  .contact-list {
    list-style: none;
    margin: 0;
    padding: 0;
  }
  .contact-item {
    position: absolute;
    left: 0;
    right: 0;
    height: 56px;
  }
  .contact-icon {
    position: absolute;
    left: 170px;
    top: 0;
    width: 56px;
    height: 56px;
  }
  .contact-label {
    position: absolute;
    left: 301px;
    top: 50%;
    transform: translateY(-50%);
    color: var(--white);
    font-size: 26px;
    letter-spacing: 0.5px;
    white-space: nowrap;
  }
  .item-name    { top: 26px; }
  .item-phone   { top: 104px; }
  .item-email   { top: 170px; }
  .item-licence { top: 231px; }
  .web-band {
    position: absolute;
    left: 0;
    right: 0;
    top: 306px;
    height: 60px;
    background: var(--gold);
    display: flex;
    align-items: center;
    justify-content: center;
    color: var(--white);
    font-size: 24px;
  }
</style>
</head>
<body>
<main class="canvas">
  <section class="card card-front">
    <h1 class="brand-name">Blue Heron Partners</h1>
  </section>

  <section class="card card-back">
    <ul class="contact-list">
      <li class="contact-item item-name">
        <svg class="contact-icon" viewBox="0 0 56 56" aria-hidden="true">
          <circle cx="28" cy="28" r="27" fill="var(--gold)"/>
          <circle cx="28" cy="22" r="7" fill="var(--navy)"/>
          <path d="M15 38 C15 31 20 29 28 29 C36 29 41 31 41 38 Z" fill="var(--navy)"/>
        </svg>
        <span class="contact-label">INDIVIDUAL NAME</span>
      </li>
      <li class="contact-item item-phone">
        <svg class="contact-icon" viewBox="0 0 56 56" aria-hidden="true">
          <path d="M6 6 L14 2 L21 14 L16 19 C19 27 25 33 33 37 L38 32 L50 40 L46 48 C44 52 38 52 32 49 C20 43 10 33 5 20 C3 14 3 9 6 6 Z" fill="var(--gold)"/>
        </svg>
        <span class="contact-label">PHONE NUMBER</span>
      </li>
      <li class="contact-item item-email">
        <svg class="contact-icon" viewBox="0 0 56 56" aria-hidden="true">
          <g fill="none" stroke="var(--gold)" stroke-width="2">
            <path d="M4 22 L28 6 L52 22 L52 52 L4 52 Z"/>
            <path d="M4 52 L24 36 M52 52 L32 36 M4 22 L28 40 L52 22"/>
          </g>
          <text x="28" y="24" text-anchor="middle" font-size="14" font-family="Arimo, Arial, sans-serif" fill="var(--white)">@</text>
        </svg>
        <span class="contact-label">E-MAIL</span>
      </li>
      <li class="contact-item item-licence">
        <svg class="contact-icon" viewBox="0 0 56 56" aria-hidden="true">
          <circle cx="23" cy="28" r="23" fill="var(--gold)"/>
          <path d="M12 28 L20 35 L33 20" fill="none" stroke="var(--navy)" stroke-width="4" stroke-linecap="round" stroke-linejoin="round"/>
        </svg>
        <span class="contact-label">LICENCE NUMBER</span>
      </li>
    </ul>
    <div class="web-band">www.blueheronpartners.com</div>
  </section>
</main>
</body>
</html>
```